Website for a Steadwell, an HVAC company.

We are a company that provides residential and commercial service. We don’t need any widgets other than a call to action where customers can message us. Though we have very few google reviews, they are all great and would like to see those populated. Simple and modern is the style. I included our logo and a pic of our vans.

Target Market(s)

Residential customers

Coding

Coded - Design and coding required

Number of Pages Required

1 page

Font styles to use
Sans Serif

Colors
0054AA
0677BA
7BADD7
CADEEF
E8F1F8
EE7325
F08F49
F5BC92
FAE3D3
FDF4ED

```html
<!DOCTYPE html>
<html lang="en">
<head>
<meta charset="utf-8">
<title>Steadwell Heating and Air</title>
<link href="https://fonts.googleapis.com/css2?family=Bebas+Neue&family=Roboto+Condensed:ital,wght@0,300;0,400;0,700;1,300&family=Roboto:wght@400;500;700;900&display=swap" rel="stylesheet">
<style>
:root{
  --blue-deep:#0054AA;
  --blue:#0677BA;
  --blue-head:#3d8fe0;
  --blue-soft:#7BADD7;
  --orange:#EE7325;
  --orange-2:#F08F49;
  --gold:#e8a33a;
  --dark:#2a2a2a;
  --dark-2:#303030;
  --ink:#1b2a4a;
  --white:#ffffff;
  --line:#d9dde3;
  --muted:#7a8290;
}
*{box-sizing:border-box;margin:0;padding:0}
html,body{width:1200px;height:2742px;overflow:hidden;background:var(--dark)}
body{position:relative;font-family:"Roboto",sans-serif;color:var(--white)}
.abs{position:absolute}
.display{font-family:"Bebas Neue",sans-serif;font-weight:400;color:var(--blue-head);line-height:1}

/* hero */
.hero{position:absolute;left:0;top:0;width:1200px;height:780px;background:var(--dark);overflow:hidden}
.hero-visual{position:absolute;left:500px;top:100px;width:690px;height:580px;border-radius:40px;
  background:linear-gradient(150deg,#3a3f4a 0%,#1a1c22 50%,#2a2320 80%,#5a3a20 100%)}
.brand{position:absolute;left:47px;top:150px;display:flex;align-items:center;gap:10px}
.brand-dot{width:28px;height:28px;border-radius:50%;background:var(--orange)}
.brand-name{font-family:"Roboto",sans-serif;font-weight:900;font-size:24px;letter-spacing:4px;color:var(--blue-head)}
.nav{position:absolute;top:45px;left:598px;display:flex;align-items:center;font-family:"Roboto Condensed",sans-serif;font-weight:700;font-size:17px}
.nav-link{color:var(--white);text-decoration:none;margin-right:38px}
.nav-phone{display:flex;align-items:center;gap:14px;margin-right:35px}
.btn-quote{display:inline-block;background:var(--white);color:var(--orange);font-family:"Roboto Condensed",sans-serif;font-weight:700;font-size:17px;line-height:20px;border-radius:4px;padding:10px 21px;text-decoration:none}
.hero-title{position:absolute;left:44px;top:282px;font-size:70px}
.hero-sub{position:absolute;left:44px;top:456px;font-family:"Roboto Condensed",sans-serif;font-weight:300;font-size:37px;line-height:44px}
.hero-cta{position:absolute;left:44px;top:580px}

/* about */
.about{position:absolute;left:0;top:780px;width:1200px;height:645px;background:var(--dark)}
.about-van{position:absolute;left:44px;top:40px;width:556px;height:490px;border-radius:40px;
  background:linear-gradient(200deg,#3a3f4a 0%,#16181d 55%,#0e1014 100%)}
.about-title{position:absolute;left:690px;top:85px;font-size:48px;line-height:48px}
.about-text{position:absolute;left:690px;top:200px;width:392px;font-family:"Roboto Condensed",sans-serif;font-weight:300;font-size:20.5px;line-height:29px}
.features{position:absolute;left:690px;top:365px;list-style:none}
.features li{display:flex;align-items:center;gap:14px;height:48px;font-family:"Roboto Condensed",sans-serif;font-size:22px}
.features svg{width:28px;height:28px}

/* reviews */
.reviews{position:absolute;left:0;top:1425px;width:1200px;height:595px;overflow:hidden}
.reviews-bg{position:absolute;inset:0;background:radial-gradient(ellipse at 50% 55%,#3b3b3b 0%,#2f2f2f 55%,#262626 100%)}
.reviews-title{position:absolute;left:0;width:1200px;top:140px;text-align:center;font-size:46px}
.quote{position:absolute;left:0;width:1200px;top:220px;text-align:center;font-family:"Roboto Condensed",sans-serif;font-style:italic;font-weight:300;font-size:41px;line-height:59px}
.stars{position:absolute;left:0;width:1200px;top:392px;display:flex;justify-content:center;gap:12px}

/* contact */
.contact{position:absolute;left:0;top:2000px;width:1200px;height:690px;overflow:hidden;background:var(--dark)}
.contact-title{position:absolute;left:100px;top:142px;font-family:"Roboto",sans-serif;font-weight:900;font-size:50px;letter-spacing:1px}
.contact-lead{position:absolute;left:100px;top:200px;width:340px;font-size:12.5px;line-height:18px}
.info{position:absolute;left:100px}
.info-icon{position:absolute;left:0;top:0;width:44px;height:44px;border-radius:50%;background:#3d3d3d;display:flex;align-items:center;justify-content:center}
.info-body{position:absolute;left:58px;top:0;width:320px}
.info-label{font-size:10.5px;font-weight:700;color:var(--orange);letter-spacing:.4px}
.info-value{font-size:17px;line-height:22px}
.info-link{font-size:9.5px;color:var(--orange);margin-top:3px}
.form-card{position:absolute;left:650px;top:147px;width:448px;height:470px;background:var(--white);border-radius:16px;color:var(--ink);padding:28px 33px}
.form-title{font-family:"Bebas Neue",sans-serif;font-size:25px;color:var(--ink)}
.form-sub{font-size:11px;color:#3a4660;margin-top:6px}
.row{display:flex;gap:12px}
.field{margin-top:15px;flex:1}
.field label{display:block;font-size:11px;margin-bottom:6px;color:var(--ink)}
.field .input{height:30px;border:1px solid var(--line);border-radius:3px;font-size:10.5px;color:#8b93a1;padding:8px 12px}
.field .area{height:70px}
.submit{display:inline-flex;align-items:center;gap:10px;margin-top:18px;background:var(--orange);color:var(--white);font-family:"Bebas Neue",sans-serif;font-size:12px;padding:13px 22px}

/* footer */
.footer{position:absolute;left:0;top:2690px;width:1200px;height:52px;background:var(--white);color:#222}
.footer-note{position:absolute;left:100px;top:19px;font-size:12px}
.social{position:absolute;right:100px;top:14px;display:flex;gap:10px}
.social span{width:26px;height:26px;border:1px solid #c9ccd1;border-radius:3px;display:block}
</style>
</head>
<body>

<section class="hero">
  <div class="hero-visual" role="img" aria-label="Steadwell service van with branded wrap, set against a warm gold and blue backdrop"></div>

  <div class="brand"><span class="brand-dot"></span><span class="brand-name">STEADWELL</span></div>

  <nav class="nav">
    <a class="nav-link" href="#">Home</a>
    <a class="nav-link" href="#">About Us</a>
    <a class="nav-link" href="#">Reviews</a>
    <span class="nav-phone">
      <svg width="26" height="26" viewBox="0 0 26 26"><circle cx="13" cy="13" r="13" fill="#fff"/><path d="M9 7c1 0 1.6 2.3 1.8 3 .1.6-1 1.1-.9 1.6.5 1.5 1.9 3 3.4 3.5.5.1 1-1 1.6-.9.7.2 3 .8 3 1.8 0 1-1.2 2.1-2.2 2.1C11 18 8 15 7 10.2 7 8.9 8 7 9 7Z" fill="#2a2a2a"/></svg>
      555.204.7310
    </span>
    <a class="btn-quote" href="#">Get a Quote</a>
  </nav>

  <h1 class="display hero-title">STEADWELL<br>HVAC SERVICES</h1>
  <p class="hero-sub">Reliable Comfort for Your<br>Home &amp; Business</p>
  <a class="btn-quote hero-cta" href="#">Get a Quote</a>
</section>

<section class="about">
  <div class="about-van" role="img" aria-label="Rear three-quarter view of the Steadwell service van"></div>
  <h2 class="display about-title">EXPERT HEATING &amp;<br>COOLING SOLUTIONS</h2>
  <p class="about-text">At Steadwell, we specialize in top-quality HVAC services for residential and commercial properties. Whether you need installation, repair, or maintenance, our experienced team ensures your comfort year-round.</p>
  <ul class="features">
    <li><svg viewBox="0 0 28 28"><circle cx="16" cy="14" r="11" fill="#EE7325"/><path d="M16 8v6l4 3" stroke="#2a2a2a" stroke-width="2" fill="none"/><path d="M2 12h7M3 16h6M4 20h6" stroke="#EE7325" stroke-width="2"/></svg>Fast &amp; Reliable Service</li>
    <li><svg viewBox="0 0 28 28"><circle cx="12" cy="8" r="5" fill="#EE7325"/><path d="M3 25c0-6 4-9 9-9s9 3 9 9Z" fill="#EE7325"/><rect x="18" y="16" width="8" height="8" rx="1" fill="#F08F49"/></svg>Professional Technicians</li>
    <li><svg viewBox="0 0 28 28"><rect x="4" y="12" width="9" height="14" fill="#F08F49"/><rect x="13" y="4" width="11" height="22" fill="#EE7325"/><path d="M16 8h2M20 8h2M16 13h2M20 13h2M16 18h2M20 18h2" stroke="#2a2a2a" stroke-width="2"/></svg>Residential &amp; Commercial Solutions</li>
  </ul>
</section>

<section class="reviews">
  <div class="reviews-bg" role="img" aria-label="Dimmed photo of a Steadwell van parked beside a building"></div>
  <h2 class="display reviews-title">WHAT OUR CUSTOMERS SAY</h2>
  <p class="quote">Steadwell lives up to their name! Quick<br>response and excellent service.</p>
  <div class="stars">
    <svg width="26" height="26" viewBox="0 0 24 24"><path d="M12 2l2.9 6.9 7.1.6-5.4 4.7 1.7 7.3L12 17.6 5.7 21.5l1.7-7.3L2 9.5l7.1-.6Z" fill="var(--gold)"/></svg>
    <svg width="26" height="26" viewBox="0 0 24 24"><path d="M12 2l2.9 6.9 7.1.6-5.4 4.7 1.7 7.3L12 17.6 5.7 21.5l1.7-7.3L2 9.5l7.1-.6Z" fill="var(--gold)"/></svg>
    <svg width="26" height="26" viewBox="0 0 24 24"><path d="M12 2l2.9 6.9 7.1.6-5.4 4.7 1.7 7.3L12 17.6 5.7 21.5l1.7-7.3L2 9.5l7.1-.6Z" fill="var(--gold)"/></svg>
    <svg width="26" height="26" viewBox="0 0 24 24"><path d="M12 2l2.9 6.9 7.1.6-5.4 4.7 1.7 7.3L12 17.6 5.7 21.5l1.7-7.3L2 9.5l7.1-.6Z" fill="var(--gold)"/></svg>
    <svg width="26" height="26" viewBox="0 0 24 24"><path d="M12 2l2.9 6.9 7.1.6-5.4 4.7 1.7 7.3L12 17.6 5.7 21.5l1.7-7.3L2 9.5l7.1-.6Z" fill="var(--gold)"/></svg>
  </div>
</section>

<section class="contact">
  <svg class="abs" style="left:0;top:0" width="1200" height="690" viewBox="0 0 1200 690">
    <path d="M0 0 H1200 V60 C1000 10 800 0 600 14 C350 30 120 80 0 150 Z" fill="#2f2f2f"/>
    <path d="M0 150 C80 60 300 25 600 14 C330 40 110 100 0 170 Z" fill="#EE7325"/>
    <path d="M820 20 C1000 20 1150 90 1200 160 V110 C1120 50 980 22 820 20 Z" fill="#242424"/>
  </svg>

  <h2 class="contact-title">GET IN TOUCH</h2>
  <p class="contact-lead">Steadwell, we specialize in top-quality HVAC services for residential and commercial properties.</p>

  <div class="info" style="top:310px">
    <div class="info-icon"><svg width="20" height="20" viewBox="0 0 20 20"><path d="M10 18s6-6 6-10a6 6 0 0 0-12 0c0 4 6 10 6 10Z" fill="none" stroke="#fff" stroke-width="1.4"/><circle cx="10" cy="8" r="2.2" fill="none" stroke="#fff" stroke-width="1.4"/></svg></div>
    <div class="info-body"><div class="info-label">LOCATION</div><div class="info-value">218 Harbor Lane Millbrook, TX 77000</div><div class="info-link">VIEW MAP</div></div>
  </div>
  <div class="info" style="top:390px">
    <div class="info-icon"><svg width="20" height="20" viewBox="0 0 20 20"><path d="M6 3c1 0 1.8 2.8 2 3.6.1.6-1.2 1.2-1 1.8.6 1.8 2 3.3 3.7 3.8.6.2 1.1-1.1 1.7-1 .8.2 3.6 1 3.6 2 0 1.1-1.4 2.6-2.6 2.6C8 15.8 4 11.8 3.6 6.4 3.6 5 5 3 6 3Z" fill="none" stroke="#fff" stroke-width="1.4"/></svg></div>
    <div class="info-body" style="top:8px"><div class="info-value">555-318-2046</div></div>
  </div>
  <div class="info" style="top:455px">
    <div class="info-icon"><svg width="20" height="20" viewBox="0 0 20 20"><rect x="2.5" y="4.5" width="15" height="11" fill="none" stroke="#fff" stroke-width="1.4"/><path d="M2.5 5l7.5 6 7.5-6" fill="none" stroke="#fff" stroke-width="1.4"/></svg></div>
    <div class="info-body"><div class="info-label">EMAIL US</div><div class="info-value">hello@steadwellair.com</div></div>
  </div>
  <div class="info" style="top:515px">
    <div class="info-icon"><svg width="20" height="20" viewBox="0 0 20 20"><circle cx="10" cy="10" r="7.5" fill="none" stroke="#fff" stroke-width="1.4"/><path d="M10 5.5V10l3 2" fill="none" stroke="#fff" stroke-width="1.4"/></svg></div>
    <div class="info-body"><div class="info-label">OPEN HOURS</div><div class="info-value">Mon - Thur 8 AM - 5 PM<br>Fri : 8 AM - 4 PM<br>Sat &amp; Sun : Closed</div></div>
  </div>

  <form class="form-card">
    <div class="form-title">CONTACT US</div>
    <div class="form-sub">Built to Last, Backed by the Best</div>
    <div class="row">
      <div class="field"><label>Name</label><div class="input">Full name</div></div>
      <div class="field"><label>Email</label><div class="input">Email adress</div></div>
    </div>
    <div class="field"><label>Company</label><div class="input">Company name</div></div>
    <div class="field"><label>Phone</label><div class="input">Phone number</div></div>
    <div class="field"><label>Message</label><div class="input area">Write message</div></div>
    <div class="submit">SUBMIT <svg width="14" height="10" viewBox="0 0 14 10"><path d="M0 5h12M8 1l4 4-4 4" fill="none" stroke="#fff" stroke-width="1.4"/></svg></div>
  </form>
</section>

<footer class="footer">
  <p class="footer-note">©2025 Steadwell Heating and Air |&nbsp; All rights reserved</p>
  <div class="social"><span></span><span></span><span></span><span></span></div>
</footer>

</body>
</html>
```